Calloway needs a modernized design

We would like a modern update (that can be responsive) to our existing website. Attached are the two existing pages we would like new concepts of - our home page and a page about one of our locations.

Calloway is provides executive offices and virtual office services. Startups, law firms, and financial services are our primary clients. We would like a professional, clean design, leaning towards minimalist. We intend to greatly reduce/eliminate the long paragraphs of text.

Requirements
Must have
• A design that can be responsive
Nice to have
• Large image(s) on home page that rotate.

```html
<!DOCTYPE html>
<html lang="en">
<head>
<meta charset="utf-8">
<title>Calloway Business Centers</title>
<link rel="stylesheet" href="https://fonts.googleapis.com/css2?family=Cinzel:wght@400;600;700&family=Lato:wght@400;700;900&family=Open+Sans:wght@400&display=swap">
<style>
:root{
  --navy:#25376b;
  --navy-deep:#1f2f5c;
  --footer:#243562;
  --orange:#f7941d;
  --orange-deep:#ec8416;
  --grey-bg:#ececec;
  --grey-line:#cfd3db;
  --text:#555a63;
  --white:#ffffff;
  --submit:#3b55a0;
}
*{margin:0;padding:0;box-sizing:border-box}
html,body{width:1200px;height:2769px;overflow:hidden;background:var(--white)}
body{font-family:"Lato",sans-serif;color:var(--text);position:relative}
.page{position:relative;width:1200px;height:2769px;overflow:hidden}
.abs{position:absolute}
.serif{font-family:"Cinzel",serif}

/* header */
.top-rule{left:0;top:0;width:1200px;height:3px;background:var(--navy)}
.brand{left:61px;top:18px;display:flex;align-items:center;gap:14px}
.brand-mark{width:78px;height:78px;border-radius:50%;background:var(--navy)}
.brand-name{font-family:"Cinzel",serif;font-weight:700;font-size:38px;color:var(--navy);letter-spacing:1px}
.socials-top{left:822px;top:8px;display:flex;gap:8px}
.socials-top span{width:24px;height:24px;border-radius:50%;display:block}
.phone-pill{left:978px;top:0;width:222px;height:33px;background:var(--navy);border-bottom-left-radius:26px;color:var(--white);font-size:18px;display:flex;align-items:center;gap:10px;padding-left:30px}
.nav{left:470px;top:64px;display:flex;align-items:center}
.nav a{font-family:"Cinzel",serif;font-size:17px;color:#222;text-decoration:none;letter-spacing:1px;padding:0 14px;border-left:1px solid #bbb;line-height:16px}
.nav a.first{border-left:none}
.nav .home{margin-right:14px}

/* hero */
.hero{left:0;top:111px;width:1200px;height:507px;background:linear-gradient(180deg,#cdc9c4 0%,#b8ada2 45%,#8a7f78 100%)}
.hero-caption{left:0;top:554px;width:1200px;height:64px;background:rgba(20,20,24,.72);color:var(--white);font-family:"Open Sans",sans-serif;font-size:36px;text-align:center;line-height:64px}
.hero-arrow{top:358px;width:26px;height:40px;background:rgba(255,255,255,.9);display:flex;align-items:center;justify-content:center}
.hero-arrow.left{left:0;border-radius:0 20px 20px 0}
.hero-arrow.right{right:0;border-radius:20px 0 0 20px}

/* welcome */
.section-title{width:1200px;left:0;text-align:center;font-family:"Cinzel",serif;font-weight:600;color:var(--navy);font-size:37px;letter-spacing:2px}
.divider{left:290px;width:620px;height:24px}
.welcome-lead{left:100px;top:752px;width:1000px;text-align:center;font-weight:700;color:var(--navy);font-size:19px;line-height:26px}
.welcome-body{left:80px;top:824px;width:1040px;text-align:center;font-size:15px;line-height:23px;color:#555}
.btn{display:flex;align-items:center;height:31px;border-radius:16px;font-size:14px;font-weight:700;padding:0 14px 0 4px;gap:8px}
.btn .dot{width:24px;height:24px;border-radius:50%}
.btn-orange{background:var(--orange);color:var(--white)}
.btn-orange .dot{background:var(--navy)}
.btn-navy{background:var(--navy);color:var(--white)}
.btn-navy .dot{background:var(--white)}

/* offering panels */
.panel{top:1006px;height:465px}
.panel-exec{left:0;width:595px;background:linear-gradient(135deg,#2f4276 0%,#25376b 55%,#1f2f5c 100%)}
.panel-virtual{left:595px;width:605px;background:linear-gradient(135deg,#f9a23a 0%,#f7941d 55%,#ec8416 100%)}
.panel-title{font-family:"Cinzel",serif;font-size:33px;letter-spacing:1px;text-align:center}
.checks{list-style:none;font-size:14px;color:var(--white);font-weight:700}
.checks li{display:flex;align-items:center;gap:8px;height:30px}
.tick{width:14px;height:14px;flex:none}

/* community / services */
.community-bg{left:0;top:1471px;width:595px;height:554px;background:linear-gradient(90deg,#f2f2f2 0%,#e6e6e6 85%,#d9d9d9 100%)}
.services-bg{left:595px;top:1471px;width:605px;height:554px;background:var(--grey-bg)}
.block-title{font-family:"Cinzel",serif;font-weight:600;font-size:36px;color:var(--navy);letter-spacing:1px}
.community-photo{left:61px;top:1602px;width:489px;height:202px;background:linear-gradient(135deg,#8a6a4c 0%,#b08a67 40%,#6b7380 100%)}
.community-text{left:61px;top:1818px;width:490px;font-size:13.5px;line-height:19px;color:#333}
.read-link{font-size:14px;font-weight:700;color:var(--navy)}
.service{left:641px;width:500px;height:137px}
.service-icon{position:absolute;left:0;top:6px;width:60px;height:60px;border-radius:50%;background:#2b2b2b;border:3px solid #d0d0d0}
.service-name{position:absolute;left:73px;top:0;font-size:20px;font-weight:700;color:var(--orange)}
.service-text{position:absolute;left:73px;top:30px;width:430px;font-size:13.5px;line-height:19px;color:#333}
.service-link{position:absolute;left:73px;top:74px}
.service-rule{position:absolute;left:0;top:122px;width:500px;border-top:1px dashed #9aa0aa}

/* partners */
.partner{top:2195px;width:157px;height:74px;border:1px solid #d8d8d8;background:var(--white);display:flex;align-items:center;justify-content:center;gap:10px}
.partner .badge-dot{width:26px;height:26px;border-radius:50%;background:#3a3a3a}
.partner .badge-bar{width:72px;height:18px;border-radius:3px;background:#4a4a4a}

/* footer */
.footer-band{left:0;top:2340px;width:1200px;height:383px}
.footer-mark{left:559px;top:2316px;width:82px;height:82px;border-radius:50%;background:var(--navy);border:5px solid var(--white);box-shadow:0 0 0 2px #c9ced8}
.foot-head{font-family:"Cinzel",serif;font-size:20px;color:var(--white);letter-spacing:1.5px}
.foot-rule{height:1px;background:rgba(255,255,255,.25)}
.foot-sep{top:2478px;width:0;height:220px;border-left:1px dotted rgba(255,255,255,.3)}
.quick-links{list-style:none;font-size:13.5px;color:var(--white)}
.quick-links li{height:35px;display:flex;align-items:center;gap:12px}
.quick-links li::before{content:"";width:5px;height:5px;border-radius:50%;background:var(--orange)}
.contact-line{font-size:13.5px;color:var(--white);line-height:20px;display:flex;gap:10px}
.contact-line svg{flex:none;margin-top:2px}
.field{left:646px;width:277px;height:38px;background:var(--white);border-radius:2px;font-size:13px;color:#777;padding:0 12px;display:flex;align-items:center}
.submit{left:646px;top:2658px;width:129px;height:37px;background:var(--submit);color:var(--white);font-weight:700;font-size:16px;display:flex;align-items:center;justify-content:center}
.follow{left:1017px;top:2525px;list-style:none}
.follow li{display:flex;align-items:center;gap:12px;height:45px;font-size:13.5px;font-weight:700;color:var(--white);letter-spacing:.5px}
.follow span{width:34px;height:34px;border-radius:50%;display:block}
.copyright{left:0;top:2723px;width:1200px;height:46px;background:var(--orange);color:var(--white);font-weight:700;font-size:13px;text-align:center;line-height:46px}
</style>
</head>
<body>
<div class="page">

  <!-- Header -->
  <div class="abs top-rule"></div>
  <div class="abs brand">
    <div class="brand-mark"></div>
    <div class="brand-name">CALLOWAY</div>
  </div>
  <div class="abs socials-top">
    <span style="background:#cb2027"></span>
    <span style="background:#0e76a8"></span>
    <span style="background:#1da1f2"></span>
    <span style="background:#dd4b39"></span>
  </div>
  <div class="abs phone-pill">
    <svg width="18" height="18" viewBox="0 0 24 24"><circle cx="12" cy="12" r="11" fill="none" stroke="#fff" stroke-width="1.6"/><path d="M8 6.5c.6-.4 1.2-.2 1.5.3l1 1.8c.3.5.1 1-.3 1.3l-.6.5c.6 1.4 1.6 2.4 3 3l.5-.6c.3-.4.8-.6 1.3-.3l1.8 1c.5.3.7.9.3 1.5-.6 1-1.6 1.4-2.7 1-3-1-5.3-3.3-6.3-6.3-.4-1.1 0-2.1 1-2.7z" fill="#fff"/></svg>
    +214.555.0147
  </div>
  <nav class="abs nav">
    <svg class="home" width="30" height="30" viewBox="0 0 30 30"><path d="M15 3 2 15h4v12h7v-8h4v8h7V15h4z" fill="var(--navy)"/></svg>
    <a class="first">Properties</a>
    <a>Virtual Tours &amp; Videos</a>
    <a>Photos</a>
    <a>Broker Referrals</a>
  </nav>

  <!-- Hero -->
  <div class="abs hero" role="img" aria-label="Photo of a presenter leading a meeting with colleagues around a conference table"></div>
  <div class="abs hero-caption">We Provide Executive Offices And Virtual Office Services</div>
  <div class="abs hero-arrow left"><svg width="10" height="14" viewBox="0 0 10 14"><path d="M8 1 2 7l6 6" fill="none" stroke="#333" stroke-width="2"/></svg></div>
  <div class="abs hero-arrow right"><svg width="10" height="14" viewBox="0 0 10 14"><path d="M2 1l6 6-6 6" fill="none" stroke="#333" stroke-width="2"/></svg></div>

  <!-- Welcome -->
  <h1 class="abs section-title" style="top:652px">WELCOME TO CALLOWAY BUSINESS CENTERS</h1>
  <svg class="abs divider" style="top:708px" viewBox="0 0 620 24"><line x1="0" y1="12" x2="292" y2="12" stroke="var(--grey-line)"/><line x1="328" y1="12" x2="620" y2="12" stroke="var(--grey-line)"/><circle cx="310" cy="12" r="11" fill="var(--navy)"/></svg>
  <p class="abs welcome-lead">Come See Why Smarter Companies are Choosing Calloway Business Centers' Dallas, Ft. Worth and Houston Executive Office Suites, Virtual Offices, Meeting Rooms and Video Conferencing.</p>
  <p class="abs welcome-body">Either you need Dallas/Ft. Worth Office Space, Dallas Executive Suites, Ft. Worth Executive Suites, Houston Office Space, Houston Executive Suites, or maybe you simply need a place to stop in and use an on-demand office or meeting room from time to time or utilize our local business phone numbers, phone answering or business addresses through one of our virtual office solutions</p>
  <div class="abs btn btn-orange" style="left:530px;top:921px"><span class="dot"></span>Read More &raquo;</div>

  <!-- Offering panels -->
  <div class="abs panel panel-exec" role="img" aria-label="Office workspace photo under a navy tint"></div>
  <div class="abs panel panel-virtual" role="img" aria-label="Office workspace photo under an orange tint"></div>
  <svg class="abs" style="left:574px;top:1006px" width="42" height="20" viewBox="0 0 42 20"><path d="M0 0h42L21 20z" fill="#fff"/></svg>
  <svg class="abs" style="left:0;top:1060px" width="1200" height="150" viewBox="0 0 1200 150">
    <line x1="380" y1="72" x2="840" y2="72" stroke="#c7cbd6" stroke-width="2"/>
    <circle cx="392" cy="72" r="5" fill="#c7cbd6"/>
    <circle cx="808" cy="72" r="5" fill="#c7cbd6"/>
    <circle cx="308" cy="72" r="64" fill="var(--orange)" stroke="#fff" stroke-width="5"/>
    <circle cx="906" cy="72" r="64" fill="var(--navy)" stroke="#fff" stroke-width="5"/>
    <circle cx="598" cy="72" r="38" fill="#fff" stroke="var(--navy)" stroke-width="4"/>
    <circle cx="598" cy="72" r="28" fill="var(--navy)"/>
    <!-- office chair -->
    <g fill="#fff">
      <rect x="290" y="38" width="36" height="32" rx="6"/>
      <rect x="284" y="74" width="48" height="9" rx="4"/>
      <rect x="305" y="83" width="6" height="14"/>
      <rect x="292" y="97" width="32" height="5" rx="2"/>
      <rect x="278" y="58" width="6" height="20" rx="3"/>
      <rect x="332" y="58" width="6" height="20" rx="3"/>
    </g>
    <!-- workstation -->
    <g fill="#fff">
      <rect x="880" y="42" width="48" height="32" rx="3"/>
      <rect x="900" y="74" width="8" height="10"/>
      <rect x="870" y="84" width="72" height="6" rx="2"/>
      <rect x="876" y="90" width="5" height="16"/>
      <rect x="931" y="90" width="5" height="16"/>
    </g>
  </svg>
  <h2 class="abs panel-title" style="left:0;top:1208px;width:595px;color:var(--orange)">EXECUTIVE OFFICES</h2>
  <h2 class="abs panel-title" style="left:595px;top:1208px;width:605px;color:var(--white)">VIRTUAL OFFICE</h2>

  <ul class="abs checks" style="left:108px;top:1268px">
    <li><svg class="tick" viewBox="0 0 14 14"><path d="M2 7l3.5 3.5L12 3" fill="none" stroke="var(--orange)" stroke-width="2.5"/></svg>Full Service Offices</li>
    <li><svg class="tick" viewBox="0 0 14 14"><path d="M2 7l3.5 3.5L12 3" fill="none" stroke="var(--orange)" stroke-width="2.5"/></svg>Disaster Recovery</li>
    <li><svg class="tick" viewBox="0 0 14 14"><path d="M2 7l3.5 3.5L12 3" fill="none" stroke="var(--orange)" stroke-width="2.5"/></svg>All-Inclusive Pricing!</li>
  </ul>
  <ul class="abs checks" style="left:292px;top:1268px">
    <li><svg class="tick" viewBox="0 0 14 14"><path d="M2 7l3.5 3.5L12 3" fill="none" stroke="var(--orange)" stroke-width="2.5"/></svg>Flexible Contracts from $395</li>
    <li><svg class="tick" viewBox="0 0 14 14"><path d="M2 7l3.5 3.5L12 3" fill="none" stroke="var(--orange)" stroke-width="2.5"/></svg>Corporate or Satellite Offices</li>
  </ul>
  <ul class="abs checks" style="left:704px;top:1268px">
    <li><svg class="tick" viewBox="0 0 14 14"><path d="M2 7l3.5 3.5L12 3" fill="none" stroke="var(--navy)" stroke-width="2.5"/></svg>Mailing Address $49/mo</li>
    <li><svg class="tick" viewBox="0 0 14 14"><path d="M2 7l3.5 3.5L12 3" fill="none" stroke="var(--navy)" stroke-width="2.5"/></svg>Local Phone &amp; Mail $99/mo</li>
    <li><svg class="tick" viewBox="0 0 14 14"><path d="M2 7l3.5 3.5L12 3" fill="none" stroke="var(--navy)" stroke-width="2.5"/></svg>Corporate or Satellite Offices</li>
  </ul>
  <ul class="abs checks" style="left:948px;top:1268px">
    <li><svg class="tick" viewBox="0 0 14 14"><path d="M2 7l3.5 3.5L12 3" fill="none" stroke="var(--navy)" stroke-width="2.5"/></svg>Flexible Contracts</li>
    <li><svg class="tick" viewBox="0 0 14 14"><path d="M2 7l3.5 3.5L12 3" fill="none" stroke="var(--navy)" stroke-width="2.5"/></svg>All-Inclusive Pricing!</li>
  </ul>
  <div class="abs btn btn-orange" style="left:237px;top:1386px"><span class="dot"></span>Read More &raquo;</div>
  <div class="abs btn btn-navy" style="left:834px;top:1386px"><span class="dot"></span>Read More &raquo;</div>

  <!-- Community -->
  <div class="abs community-bg"></div>
  <div class="abs services-bg"></div>
  <h2 class="abs block-title" style="left:61px;top:1515px">COMMUNITY</h2>
  <div class="abs community-photo" role="img" aria-label="Photo of many hands stacked together over a wooden table"></div>
  <p class="abs community-text">Our members share more than a front desk. Monthly breakfasts, lunch-and-learn sessions and after-hours mixers bring founders, attorneys and advisors together under one roof, so the people down the hall quickly become clients, partners and friends. Each center keeps a calendar of open events, and every member is welcome to host a talk, meet a mentor or simply trade ideas over a good cup of coffee.</p>
  <div class="abs read-link" style="left:63px;top:1955px">Read More &raquo;</div>

  <h2 class="abs block-title" style="left:641px;top:1515px;font-size:33px">OTHER SERVICES</h2>
  <div class="abs service" style="top:1605px">
    <div class="service-icon"><svg width="54" height="54" viewBox="0 0 54 54"><rect x="17" y="22" width="20" height="10" rx="2" fill="#fff"/><circle cx="20" cy="16" r="3" fill="#fff"/><circle cx="34" cy="16" r="3" fill="#fff"/><circle cx="20" cy="38" r="3" fill="#fff"/><circle cx="34" cy="38" r="3" fill="#fff"/></svg></div>
    <div class="service-name">On-demand Meeting Rooms</div>
    <p class="service-text">Book a polished room by the hour, with screens, coffee service and a receptionist to greet your guests.</p>
    <div class="service-link read-link">Read More &raquo;</div>
    <div class="service-rule"></div>
  </div>
  <div class="abs service" style="top:1742px">
    <div class="service-icon"><svg width="54" height="54" viewBox="0 0 54 54"><circle cx="27" cy="27" r="9" fill="#fff"/><circle cx="27" cy="12" r="3" fill="#fff"/><circle cx="27" cy="42" r="3" fill="#fff"/><circle cx="12" cy="27" r="3" fill="#fff"/><circle cx="42" cy="27" r="3" fill="#fff"/></svg></div>
    <div class="service-name">On-demand Training Rooms</div>
    <p class="service-text">Train your team in a bright classroom setup with projector, whiteboards and flexible seating for every size.</p>
    <div class="service-link read-link">Read More &raquo;</div>
    <div class="service-rule"></div>
  </div>
  <div class="abs service" style="top:1879px">
    <div class="service-icon"><svg width="54" height="54" viewBox="0 0 54 54"><rect x="15" y="14" width="24" height="16" rx="2" fill="#fff"/><rect x="24" y="30" width="6" height="5" fill="#fff"/><rect x="13" y="36" width="28" height="4" rx="2" fill="#fff"/></svg></div>
    <div class="service-name">Virtual Office Solutions</div>
    <p class="service-text">Get a prestigious address, local phone number and live call answering without leasing a full office.</p>
    <div class="service-link read-link">Read More &raquo;</div>
  </div>

  <!-- Partners -->
  <h2 class="abs section-title" style="top:2075px;font-size:36px">OUR PARTNERS</h2>
  <svg class="abs divider" style="top:2126px" viewBox="0 0 620 24"><line x1="0" y1="12" x2="292" y2="12" stroke="var(--grey-line)"/><line x1="328" y1="12" x2="620" y2="12" stroke="var(--grey-line)"/><circle cx="310" cy="12" r="11" fill="var(--navy)"/></svg>
  <svg class="abs" style="left:16px;top:2208px" width="22" height="48" viewBox="0 0 22 48"><path d="M20 2 3 24l17 22" fill="none" stroke="#c4c4c4" stroke-width="2"/></svg>
  <svg class="abs" style="left:1162px;top:2208px" width="22" height="48" viewBox="0 0 22 48"><path d="M2 2l17 22L2 46" fill="none" stroke="#c4c4c4" stroke-width="2"/></svg>
  <div class="abs partner" style="left:61px"><span class="badge-dot"></span><span class="badge-bar"></span></div>
  <div class="abs partner" style="left:245px"><span class="badge-dot"></span><span class="badge-bar"></span></div>
  <div class="abs partner" style="left:429px"><span class="badge-dot"></span><span class="badge-bar"></span></div>
  <div class="abs partner" style="left:613px"><span class="badge-bar" style="width:96px"></span></div>
  <div class="abs partner" style="left:797px"><span class="badge-dot"></span><span class="badge-bar"></span></div>
  <div class="abs partner" style="left:982px"><span class="badge-bar" style="width:96px"></span></div>

  <!-- Footer -->
  <svg class="abs footer-band" viewBox="0 0 1200 383" preserveAspectRatio="none">
    <path d="M0 80 Q600 -40 1200 80 V383 H0z" fill="#c9ced8"/>
    <path d="M0 88 Q600 -28 1200 88 V383 H0z" fill="var(--footer)"/>
  </svg>
  <div class="abs footer-mark"></div>

  <h3 class="abs foot-head" style="left:61px;top:2466px">QUICK LINKS</h3>
  <h3 class="abs foot-head" style="left:310px;top:2466px">CONTACT DETAILS</h3>
  <h3 class="abs foot-head" style="left:642px;top:2466px">QUICK CONTACT</h3>
  <h3 class="abs foot-head" style="left:1017px;top:2466px">FOLLOW US</h3>
  <div class="abs foot-rule" style="left:61px;top:2505px;width:190px"></div>
  <div class="abs foot-rule" style="left:310px;top:2505px;width:270px"></div>
  <div class="abs foot-rule" style="left:642px;top:2505px;width:300px"></div>
  <div class="abs foot-rule" style="left:1017px;top:2505px;width:130px"></div>
  <div class="abs foot-sep" style="left:273px"></div>
  <div class="abs foot-sep" style="left:600px"></div>
  <div class="abs foot-sep" style="left:965px"></div>

  <ul class="abs quick-links" style="left:61px;top:2514px">
    <li>Home</li>
    <li>Properties</li>
    <li>Virtual Tours &amp; Videos</li>
    <li>Photos</li>
    <li>Broker Referrals</li>
  </ul>

  <div class="abs contact-line" style="left:310px;top:2520px">
    <svg width="13" height="17" viewBox="0 0 13 17"><path d="M6.5 0C2.9 0 0 2.8 0 6.3 0 11 6.5 17 6.5 17S13 11 13 6.3C13 2.8 10.1 0 6.5 0z" fill="var(--orange)"/><circle cx="6.5" cy="6.3" r="2.4" fill="var(--footer)"/></svg>
    <div><b>CALLOWAY BUSINESS CENTERS</b><br>4120 Harwell Avenue<br>Suite 300 , Dallas, Texas 75204</div>
  </div>
  <div class="abs contact-line" style="left:310px;top:2600px">
    <svg width="14" height="14" viewBox="0 0 24 24"><path d="M5 2c1-.6 2-.3 2.5.5l1.7 3c.5.8.2 1.7-.5 2.2l-1 .8c1 2.4 2.7 4 5 5l.8-1c.5-.7 1.4-1 2.2-.5l3 1.7c.8.5 1.1 1.5.5 2.5-1 1.7-2.7 2.4-4.5 1.8C9.7 16.3 6 12.6 4.3 7.5 3.7 5.7 4.3 3 5 2z" fill="var(--orange)"/></svg>
    <div>+ 214.555.0147</div>
  </div>
  <div class="abs contact-line" style="left:310px;top:2633px">
    <svg width="15" height="14" viewBox="0 0 15 14"><rect x="3" y="0" width="9" height="4" fill="var(--orange)"/><rect x="0" y="4" width="15" height="7" rx="1.5" fill="var(--orange)"/><rect x="3" y="9" width="9" height="5" fill="#fff"/></svg>
    <div>+ 214.555.0147</div>
  </div>
  <div class="abs contact-line" style="left:310px;top:2676px">
    <svg width="15" height="11" viewBox="0 0 15 11"><rect width="15" height="11" rx="1" fill="var(--orange)"/><path d="M0 0l7.5 6L15 0" fill="none" stroke="var(--footer)" stroke-width="1.3"/></svg>
    <div>Offices@CallowayOffices.com</div>
  </div>

  <div class="abs field" style="top:2524px">Name</div>
  <div class="abs field" style="top:2568px">Email</div>
  <div class="abs field" style="top:2612px">Message</div>
  <div class="abs submit">Submit</div>

  <ul class="abs follow">
    <li><span style="background:#dd4b39"></span>CIRCLEFEED</li>
    <li><span style="background:#1da1f2"></span>CHIRPER</li>
    <li><span style="background:#0e76a8"></span>LINKWORK</li>
    <li><span style="background:#cb2027"></span>PINBOARD</li>
  </ul>

  <div class="abs copyright">Copyright &copy; 2016&nbsp; Calloway Business Centers. All Rights Reserved.</div>
</div>
</body>
</html>
```